Business Card Design Project

Looking to update our business cards. We have a logo with our slogan. We are an IT firm so we wouldlike a modern look.

Industry/Entity Type

Business

```html
<!DOCTYPE html>
<html lang="en">
<head>
<meta charset="utf-8">
<title>Kelvane Business Card</title>
<link rel="stylesheet" href="https://fonts.googleapis.com/css2?family=Didact+Gothic&family=Tinos&display=swap">
<style>
  :root {
    --page-bg: #e9e9e6;
    --green-edge: #4e6a30;
    --green-glow: #3f9a4a;
    --green-ink: #4d6a2e;
    --name-ink: #3b5122;
    --accent: #8cc63f;
    --band-top: #f4f4f4;
    --band-mid: #e2e2e2;
    --band-bottom: #cfcfcf;
    --tagline-ink: #1e1e1e;
    --light-text: #ffffff;
  }
  * { margin: 0; padding: 0; box-sizing: border-box; }
  html, body { width: 1200px; height: 1181px; overflow: hidden; }
  body { background: var(--page-bg); position: relative; }

  .card {
    position: absolute;
    left: 212px;
    width: 776px;
    height: 447px;
    overflow: hidden;
    background: radial-gradient(ellipse 330px 300px at 50% 50%, var(--green-glow) 0%, #458a3f 35%, var(--green-edge) 100%);
    box-shadow: 0 4px 10px rgba(0,0,0,0.25);
  }
  .card--front { top: 103px; }
  .card--back { top: 622px; }

  .band {
    position: absolute;
    left: 0; right: 0;
    height: 110px;
    background: linear-gradient(to bottom, var(--band-top) 0%, var(--band-mid) 60%, var(--band-bottom) 100%);
    box-shadow: 0 3px 4px rgba(0,0,0,0.25);
  }
  .card--front .band { top: 169px; }
  .card--back .band { top: 168px; }

  .brand {
    position: absolute;
    top: 188px; left: 0; right: 0;
    text-align: center;
    font-family: "Didact Gothic", sans-serif;
  }
  .brand__name {
    display: inline-flex;
    align-items: center;
    gap: 14px;
    font-size: 54px;
    letter-spacing: 12px;
    color: var(--green-ink);
    line-height: 1;
  }
  .brand__dot {
    width: 30px; height: 30px;
    border-radius: 50%;
    background: var(--accent);
  }
  .brand__tagline {
    margin-top: 6px;
    font-size: 16px;
    letter-spacing: 6.4px;
    color: var(--tagline-ink);
    -webkit-text-stroke: 0.4px var(--tagline-ink);
  }

  .socials {
    position: absolute;
    top: 14px; right: 18px;
    display: flex; gap: 10px;
    font-family: "Tinos", serif;
    font-size: 14px;
    color: var(--light-text);
  }
  .socials__item { display: flex; align-items: center; gap: 7px; }
  .socials__mark { width: 20px; height: 20px; background: rgba(255,255,255,0.35); }

  .person__name {
    position: absolute;
    top: 201px; left: 0; right: 0;
    text-align: center;
    font-family: "Tinos", serif;
    font-size: 43px;
    color: var(--name-ink);
  }
  .person__title {
    position: absolute;
    top: 282px; left: 401px;
    font-family: "Tinos", serif;
    font-size: 24px;
    color: var(--light-text);
  }

  .contact {
    position: absolute;
    bottom: 8px; left: 0; right: 0;
    font-family: "Tinos", serif;
    font-size: 17px;
    color: var(--light-text);
  }
  .contact__item { position: absolute; bottom: 0; display: flex; align-items: center; gap: 8px; white-space: nowrap; }
  .contact__item--phone { left: 62px; }
  .contact__item--web { left: 285px; }
  .contact__item--email { left: 538px; }
  .contact__sep { width: 9px; height: 9px; background: var(--light-text); }
</style>
</head>
<body>
  <section class="card card--front">
    <div class="band"></div>
    <div class="brand">
      <div class="brand__name"><span>KELVANE</span><span class="brand__dot"></span></div>
      <div class="brand__tagline">MAKING TECHNOLOGY EASIER</div>
    </div>
  </section>

  <section class="card card--back">
    <div class="socials">
      <div class="socials__item"><span class="socials__mark"></span>Friendsite.com/kelvaneinc</div>
      <div class="socials__item"><span class="socials__mark"></span>Chirpnet.com/kelvaneinc</div>
    </div>
    <div class="band"></div>
    <div class="person__name">Your Name</div>
    <div class="person__title">Your Title</div>
    <div class="contact">
      <div class="contact__item contact__item--phone">Phone <span class="contact__sep"></span> 0123456789</div>
      <div class="contact__item contact__item--web">Web <span class="contact__sep"></span> www.website.com</div>
      <div class="contact__item contact__item--email">Email <span class="contact__sep"></span> name@email.com</div>
    </div>
  </section>
</body>
</html>
```